Stage Design Company Business Card

We are looking to step up up our business card design for our team.

We are a Full service Design and Consultation company for Stage and TV with an emphasis in Theatrical Lighting.

We like our materials to be clean and modern with solid colors free of patterns and gradients. Our brand consists of 4 primary colors Purple, Black, Grey, and White. Provided is our Word Mark as well as our Symbol Logo.

We would like our cards to leave an impression beyond the information, show our attention to design and detail, and make our marks an easily recognized feature (together or apart) for our clients.

We need a warm approachable comfortable feel for some clients, and a professional flair for the board member type clients.

Attached are our brand elements, and our existing cards to give a sense of our style and a glipse at the information we provide on our cards.

Target Market(s)

broad client base from church leaders to high school teachers and architects.

Industry/Entity Type

Business

Contact Information for Business Card

We format our phone number with periods not parenthesis or dashes. Information will be edited for each of our team members, and team member specific cards are not part of this scope, but rather a template so to speak.

Font styles to use
Sans Serif

Colors
6b449b
ffffff
000000
333333
aaaaaa

Requirements
Must have
• Wordmark and logo mark present (does not need to exist on the same side of card)
• Brand Colors,
• Name, Phone, Email, Address.
• Unique choices that make someone stop and take a second look
Nice to have
• It would be nice to somehow convey what we DO, as our brand name does not lend itself to this, outside of an obvious tagline though.....
• social media if not crowded. all of our handles match (instagram, twitter, facebook)
Should not have
• "clipart"

```html
<!DOCTYPE html>
<html lang="en">
<head>
<meta charset="utf-8">
<title>Halvern Stagecraft Business Card</title>
<link href="https://fonts.googleapis.com/css2?family=Jost:wght@400;600&display=swap" rel="stylesheet">
<style>
  :root {
    --purple: #3d2770;
    --ink: #111111;
    --text: #333333;
    --grey: #aaaaaa;
    --paper: #ffffff;
    --backdrop: #8e8d8e;
  }
  html, body {
    margin: 0;
    width: 1200px;
    height: 929px;
    overflow: hidden;
    background: var(--backdrop);
    font-family: "Jost", sans-serif;
  }
  .stage {
    position: relative;
    width: 1200px;
    height: 929px;
  }
  .card {
    position: absolute;
    left: 300px;
    width: 600px;
    height: 343px;
    background: var(--paper);
    box-shadow: 0 6px 18px rgba(0,0,0,0.25);
  }
  .card-front { top: 92px; }
  .card-back { top: 494px; }

  .brand {
    position: absolute;
    display: flex;
    flex-direction: column;
    align-items: center;
    gap: 14px;
  }
  .card-front .brand {
    left: 0; right: 0; top: 112px;
  }
  .brand-dot {
    width: 44px;
    height: 44px;
    border-radius: 50%;
    background: var(--purple);
  }
  .brand-name {
    font-weight: 600;
    font-size: 26px;
    letter-spacing: 0.32em;
    color: var(--ink);
    text-align: center;
    line-height: 1.25;
  }
  .brand-name span { display: block; font-size: 13px; letter-spacing: 0.5em; }

  .card-back .brand {
    left: 40px; top: 98px; width: 250px;
  }
  .card-back .brand-name { font-size: 22px; }
  .card-back .brand-name span { font-size: 11px; }

  .divider {
    position: absolute;
    left: 306px; top: 70px;
    width: 1.5px; height: 200px;
    background: var(--purple);
  }
  .details {
    position: absolute;
    left: 332px; top: 66px;
    color: var(--text);
    font-size: 15px;
    line-height: 1.3;
  }
  .person-name {
    margin: 0;
    font-weight: 600;
    font-size: 24px;
    color: var(--purple);
    line-height: 1.05;
  }
  .person-role { margin: 0 0 14px; font-size: 16px; }
  .address { margin: 0 0 12px 22px; font-style: normal; }
  .contact-list { list-style: none; margin: 0; padding: 0; }
  .contact-list li { display: flex; align-items: center; gap: 10px; }
  .contact-list svg { width: 12px; height: 12px; flex: none; }
</style>
</head>
<body>
<main class="stage">
  <section class="card card-front" aria-label="Card front">
    <div class="brand">
      <div class="brand-dot"></div>
      <div class="brand-name">HALVERN<span>STAGECRAFT</span></div>
    </div>
  </section>

  <section class="card card-back" aria-label="Card back">
    <div class="brand">
      <div class="brand-dot"></div>
      <div class="brand-name">HALVERN<span>STAGECRAFT</span></div>
    </div>
    <div class="divider"></div>
    <div class="details">
      <h1 class="person-name">MARA L QUINN</h1>
      <p class="person-role">Owner</p>
      <address class="address">112 E. Alder ST<br>Tempe, AZ 85281</address>
      <ul class="contact-list">
        <li>
          <svg viewBox="0 0 12 12" aria-hidden="true"><rect x="3" y="1" width="6" height="10" rx="1" fill="none" stroke="var(--purple)" stroke-width="1.3"/></svg>
          800.555.0142
        </li>
        <li>
          <svg viewBox="0 0 12 12" aria-hidden="true"><rect x="1" y="3" width="10" height="7" fill="var(--purple)"/><path d="M1 3 L6 7 L11 3" fill="none" stroke="#fff" stroke-width="1"/></svg>
          info@halvern-s.com
        </li>
        <li>
          <svg viewBox="0 0 12 12" aria-hidden="true"><circle cx="5" cy="5" r="3.3" fill="none" stroke="var(--purple)" stroke-width="1.6"/><path d="M7.5 7.5 L11 11" stroke="var(--purple)" stroke-width="1.8"/></svg>
          halvern-s.com
        </li>
      </ul>
    </div>
  </section>
</main>
</body>
</html>
```